Penfield Draft Works (PDWorks.net)

We need a Wordpress-based site designed for a client who provides writing and editing services for the IT industry. We have a wireframe complete for the homepage, but need all internal pages designed (based on homepage wireframe) and the entire site coded for WP.

Internal pages include: "Our Work" (with samples & testimonials); "Capabilities" (with sections to address "strategy", "coaching", "writing" and "editing"); "About Us"; and a Contact page.

Will provide all copywriting, writing samples, testimonials, and client logos.

We completely realize/acknowledge the subject matter is visually BORING! Anything at all that can be done to make it look visually appealing would be *great*! Stock photography is fine.

Please feel free to ask any questions whatsoever. Thanks for your time!

```html
<!DOCTYPE html>
<html lang="en">
<head>
<meta charset="utf-8">
<title>Penfield Draft Works</title>
<link href="https://fonts.googleapis.com/css2?family=Barlow:wght@500;600;700&family=Roboto:wght@400;500&display=swap" rel="stylesheet">
<style>
:root{
  --orange:#f26b21;
  --orange-soft:#f58a4b;
  --ink:#111111;
  --text:#444444;
  --light:#f1f1f1;
  --white:#ffffff;
  --black:#000000;
}
*{box-sizing:border-box;margin:0;padding:0}
html,body{width:1200px;height:3957px;overflow:hidden}
body{font-family:"Roboto",sans-serif;color:var(--text);background:var(--white);position:relative}
h1,h2,h3,.btn,.brand,.nav a{font-family:"Barlow",sans-serif}
.btn{display:inline-flex;align-items:center;justify-content:center;background:var(--orange);color:var(--white);border-radius:30px;font-weight:600;text-decoration:none;font-size:16px}
.section-title{font-size:35px;font-weight:600;color:var(--ink);text-align:center}

/* header */
.site-header{height:88px;border-top:4px solid var(--orange);display:flex;align-items:center;padding:0 111px;position:relative}
.brand{display:flex;align-items:center;gap:10px;font-size:23px;font-weight:700;color:var(--ink)}
.brand-mark{width:14px;height:14px;background:var(--orange)}
.nav{display:flex;gap:40px;margin-left:auto;margin-right:38px}
.nav a{font-size:16px;color:#333;text-decoration:none;font-weight:500}
.nav a.active{color:var(--orange)}
.site-header .btn{width:150px;height:46px}

/* hero */
.hero{height:634px;position:relative;background:linear-gradient(135deg,#3a2a22 0%,#6a5a50 30%,#b9b4ae 55%,#4b4440 80%,#2a2220 100%);overflow:hidden}
.hero-panel{position:absolute;left:243px;top:153px;width:711px;height:312px;background:rgba(90,90,90,.55);border-radius:8px;text-align:center;color:var(--white);padding-top:30px}
.hero-panel h1{font-size:44px;font-weight:600;line-height:53px}
.hero-panel p{font-size:15px;line-height:27px;margin:14px auto 0;width:520px}
.hero-panel .btn{width:152px;height:52px;margin-top:22px}
.hero-wave{position:absolute;left:0;bottom:0}

/* capabilities */
.capabilities{height:673px;padding-top:80px}
.cap-grid{display:flex;gap:12px;margin:40px 0 0 111px}
.cap-card{width:235px;height:325px;position:relative;background:linear-gradient(180deg,#6b6b6b,#1c1c1c);color:var(--white);text-align:center;display:flex;flex-direction:column;justify-content:flex-end;padding:0 18px 24px}
.cap-card.writing{background:linear-gradient(180deg,#d98a2c,#5c3a1a 70%,#1a120c)}
.cap-card.editing{background:linear-gradient(180deg,#8a8a80,#2a2520 70%,#0e0c0a)}
.cap-card.featured{background:var(--orange-soft);justify-content:center;padding-bottom:20px}
.cap-card h3{font-size:22px;font-weight:600;margin-bottom:10px}
.cap-card p{font-size:14.5px;line-height:26px}
.cap-card a{color:var(--white);font-family:"Barlow",sans-serif;font-weight:600;font-size:15px;margin-top:8px}
.capabilities .center{text-align:center;margin-top:49px}
.capabilities .btn{width:215px;height:52px}

/* clients */
.clients{height:295px;background:var(--light);padding-top:62px;position:relative}
.logo-row{display:flex;gap:33px;margin:38px 0 0 140px}
.logo-tile{width:203px;height:77px;background:var(--white);box-shadow:0 2px 6px rgba(0,0,0,.12);display:flex;align-items:center;justify-content:center;gap:8px;font-family:"Roboto",sans-serif;font-weight:500;font-size:16px;color:#666}
.logo-tile .dot{width:12px;height:12px;background:#999}
.arrow{position:absolute;top:169px;font-size:22px;color:#777}

/* work */
.work{height:1418px;padding-top:80px}
.work-row{position:absolute;left:111px;width:980px;height:343px;display:flex;gap:32px;align-items:center}
.work-row.reverse{flex-direction:row-reverse}
.work-copy{width:475px}
.work-copy h3{font-size:22px;font-weight:600;line-height:33px;color:var(--ink)}
.work-copy p{font-size:15px;line-height:26px;margin-top:14px}
.work-copy .btn{width:147px;height:52px;margin-top:28px}
.work-copy .btn.wide{width:167px}

/* contact band */
.contact-band{position:absolute;top:3108px;left:0;width:1200px;height:460px;display:flex}
.contact-left{width:600px;background:linear-gradient(135deg,#f58a4b,#f26b21);text-align:center;padding-top:85px;color:var(--white)}
.contact-right{width:600px;background:linear-gradient(135deg,#3c3c40,#6e7078 60%,#2a2a2e);text-align:center;padding-top:96px;color:var(--white)}
.contact-band h2{font-size:35px;font-weight:600;line-height:50px}
.contact-left .btn{background:var(--white);color:var(--orange);width:166px;height:52px;margin-top:30px}
.signup{width:386px;height:48px;background:var(--white);margin:23px 0 0 102px;display:flex;align-items:center;justify-content:space-between;padding:0 20px;color:#777;font-size:15px;border-radius:2px}
.band-wave{position:absolute;top:3430px;left:0}

/* footer */
.site-footer{position:absolute;top:3548px;left:0;width:1200px;height:409px;background:var(--black);color:var(--white)}
.foot-address{position:absolute;left:160px;top:82px;width:260px;text-align:center;font-size:14.5px;line-height:26px}
.foot-brand{position:absolute;left:0;width:1200px;top:64px;justify-content:center;color:var(--white);font-size:38px}
.foot-brand .brand-mark{width:20px;height:20px}
.foot-contact{position:absolute;left:839px;top:74px;font-size:15px;line-height:35px}
.foot-contact div{display:flex;align-items:center;gap:10px}
.foot-links{position:absolute;left:163px;top:218px;width:886px;height:78px;border-top:1px solid #333;border-bottom:1px solid #333;display:flex;justify-content:center;align-items:center;gap:65px}
.foot-links a{color:var(--white);text-decoration:none;font-size:15px}
.copyright{position:absolute;top:343px;width:1200px;text-align:center;font-size:15px}
</style>
</head>
<body>

<header class="site-header">
  <div class="brand"><span class="brand-mark"></span>Penfield Draft Works</div>
  <nav class="nav">
    <a href="#" class="active">Home</a><a href="#">Our Work</a><a href="#">Capabilities</a><a href="#">About Us</a><a href="#">Blog</a>
  </nav>
  <a class="btn" href="#">Get in touch</a>
</header>

<section class="hero" role="img" aria-label="Overhead photo of hands working at a laptop beside printed charts and documents">
  <div class="hero-panel">
    <h1>Communicate Your Expertise And<br>Your Customer Successes</h1>
    <p>Lorem ipsum dolor sit amet, consectetur adipiscing elit, sed do eiusmod tempor incididunt ut labore et dolore magna aliqua.</p>
    <a class="btn" href="#">Get Started</a>
  </div>
  <svg class="hero-wave" width="1200" height="120" viewBox="0 0 1200 120">
    <path d="M0 110 C150 20 300 10 460 60 C620 110 760 110 900 60 C1020 20 1120 20 1200 50 V120 H0 Z" fill="var(--orange)"/>
    <path d="M0 120 C150 38 300 30 460 80 C620 125 760 125 900 80 C1020 42 1120 40 1200 72 V120 Z" fill="var(--white)"/>
  </svg>
</section>

<section class="capabilities">
  <h2 class="section-title">Our Capabilities</h2>
  <div class="cap-grid">
    <div class="cap-card strategy" role="img" aria-label="Photo of colleagues discussing a strategy at a desk">
      <h3>Strategy</h3><p>Lorem ipsum dolor sit amet, consectetur adipiscing elit, sed do eiusmod.</p>
    </div>
    <div class="cap-card featured" role="img" aria-label="Photo of a coach wearing a headset at a desk">
      <h3>Coaching</h3><p>Lorem ipsum dolor sit amet, consectetur adipiscing elit, sed do eiusmod.</p><a href="#">Learn More</a>
    </div>
    <div class="cap-card writing" role="img" aria-label="Photo of a hand writing with a pen">
      <h3>Writing</h3><p>Lorem ipsum dolor sit amet, consectetur adipiscing elit, sed do eiusmod.</p>
    </div>
    <div class="cap-card editing" role="img" aria-label="Photo of an editor reviewing a printed page">
      <h3>Editing</h3><p>Lorem ipsum dolor sit amet, consectetur adipiscing elit, sed do eiusmod.</p>
    </div>
  </div>
  <div class="center"><a class="btn" href="#">View Our Capabilities</a></div>
</section>

<section class="clients">
  <h2 class="section-title">Client Logo</h2>
  <span class="arrow" style="left:52px">&#8249;</span>
  <div class="logo-row">
    <div class="logo-tile"><span class="dot"></span>Larder Co</div>
    <div class="logo-tile"><span class="dot"></span>Quillguard</div>
    <div class="logo-tile"><span class="dot"></span>Foldline</div>
    <div class="logo-tile"><span class="dot"></span>Inkwell Studio</div>
  </div>
  <span class="arrow" style="left:1138px">&#8250;</span>
</section>

<section class="work">
  <h2 class="section-title">Our Work</h2>

  <div class="work-row" style="top:1873px">
    <svg width="473" height="343" viewBox="0 0 473 343" role="img" aria-label="Photo of a man in headphones working on a laptop at a desk">
      <defs><linearGradient id="workA" x1="0" y1="0" x2="1" y2="1"><stop offset="0" stop-color="#5c6a72"/><stop offset=".5" stop-color="#b8b2a6"/><stop offset="1" stop-color="#e4e1da"/></linearGradient></defs>
      <path d="M0 0 H440 C475 50 425 110 450 171 C478 235 420 290 445 343 H0 Z" fill="url(#workA)"/>
      <path d="M440 0 C475 50 425 110 450 171 C478 235 420 290 445 343" fill="none" stroke="var(--orange)" stroke-width="4"/>
    </svg>
    <div class="work-copy">
      <h3>How to Align Your Applications to the Optimal Infrastructure Environments</h3>
      <p>Lorem ipsum dolor sit amet, consectetur adipiscing elit, sed do eiusmod tempor incididunt ut labore et dolore magna aliqua. Quis ipsum suspendisse ultrices gravida. Risus commodo viverra maecenas accumsan lacus vel facilisis. Lorem ipsum dolor sit amet, consectetur adipiscing elit, sed do eiusmod tempor</p>
      <a class="btn" href="#">Learn More</a>
    </div>
  </div>

  <div class="work-row reverse" style="top:2276px">
    <svg width="475" height="343" viewBox="0 0 475 343" role="img" aria-label="Photo of hands reviewing a document on a wooden table">
      <defs><linearGradient id="workB" x1="0" y1="0" x2="1" y2="1"><stop offset="0" stop-color="#2f4a66"/><stop offset=".5" stop-color="#9a7a5a"/><stop offset="1" stop-color="#5a3a22"/></linearGradient></defs>
      <path d="M33 0 H475 V343 H30 C0 290 55 235 25 171 C0 110 50 50 33 0 Z" fill="url(#workB)"/>
      <path d="M33 0 C50 50 0 110 25 171 C55 235 0 290 30 343" fill="none" stroke="var(--orange)" stroke-width="4"/>
    </svg>
    <div class="work-copy">
      <h3>Lorem ipsum dolor sit amet, consectetur adipiscing elit sed do</h3>
      <p>Lorem ipsum dolor sit amet, consectetur adipiscing elit, sed do eiusmod tempor incididunt ut labore et dolore magna aliqua. Quis ipsum suspendisse ultrices gravida. Risus commodo viverra maecenas accumsan lacus vel facilisis. Lorem ipsum dolor sit amet, consectetur adipiscing elit, sed do eiusmod tempor</p>
      <a class="btn" href="#">Learn More</a>
    </div>
  </div>

  <div class="work-row" style="top:2678px">
    <svg width="473" height="343" viewBox="0 0 473 343" role="img" aria-label="Photo of two colleagues in conversation at a meeting table">
      <defs><linearGradient id="workC" x1="0" y1="0" x2="1" y2="1"><stop offset="0" stop-color="#c9ccc4"/><stop offset=".5" stop-color="#6c7276"/><stop offset="1" stop-color="#2e3438"/></linearGradient></defs>
      <path d="M0 0 H440 C475 50 425 110 450 171 C478 235 420 290 445 343 H0 Z" fill="url(#workC)"/>
      <path d="M440 0 C475 50 425 110 450 171 C478 235 420 290 445 343" fill="none" stroke="var(--orange)" stroke-width="4"/>
    </svg>
    <div class="work-copy">
      <h3>Lorem ipsum dolor sit amet, consectetur adipiscing elit sed do</h3>
      <p>Lorem ipsum dolor sit amet, consectetur adipiscing elit, sed do eiusmod tempor incididunt ut labore et dolore magna aliqua. Quis ipsum suspendisse ultrices gravida. Risus commodo viverra maecenas accumsan lacus vel facilisis. Lorem ipsum dolor sit amet, consectetur adipiscing elit, sed do eiusmod tempor</p>
      <a class="btn wide" href="#">View Our Work</a>
    </div>
  </div>
</section>

<section class="contact-band">
  <div class="contact-left" role="img" aria-label="Orange-toned photo of a desk with a monitor">
    <h2>Feel free to contact us<br>with any questions.<br>We're happy to help.</h2>
    <a class="btn" href="#">Get in Touch</a>
  </div>
  <div class="contact-right" role="img" aria-label="Dark-toned photo of a hand writing in a notebook">
    <h2>Editorial inspiration delivered<br>straight to your inbox.</h2>
    <div class="signup"><span>Email Address</span>
      <svg width="16" height="16" viewBox="0 0 16 16"><path d="M15 1 L1 7 L6 9 L8 15 Z" fill="var(--orange)"/></svg>
    </div>
  </div>
</section>

<svg class="band-wave" width="1200" height="130" viewBox="0 0 1200 130">
  <path d="M0 80 C180 140 360 120 560 50 C720 0 900 20 1050 70 C1120 90 1170 60 1200 30 V130 H0 Z" fill="var(--black)"/>
  <path d="M0 80 C180 140 360 120 560 50 C720 0 900 20 1050 70 C1120 90 1170 60 1200 30" fill="none" stroke="var(--white)" stroke-width="9"/>
</svg>

<footer class="site-footer">
  <div class="foot-address">
    <svg width="16" height="22" viewBox="0 0 16 22" style="display:block;margin:0 auto 12px"><path d="M8 0 C3.6 0 0 3.4 0 7.8 C0 13 8 22 8 22 C8 22 16 13 16 7.8 C16 3.4 12.4 0 8 0 Z" fill="var(--orange)"/><circle cx="8" cy="8" r="3" fill="var(--black)"/></svg>
    Lorem ipsum dolor sit amet, consectetur adipiscing elit, sed do eiusmod tempor incididunt
  </div>
  <div class="brand foot-brand"><span class="brand-mark"></span>Penfield Draft Works</div>
  <div class="foot-contact">
    <div><svg width="14" height="14" viewBox="0 0 14 14"><path d="M3 0 L5 4 L3.5 5.5 C4.5 7.5 6.5 9.5 8.5 10.5 L10 9 L14 11 L12.5 14 C6 13.5 0.5 8 0 1.5 Z" fill="var(--orange)"/></svg>555-014-2290</div>
    <div><svg width="14" height="11" viewBox="0 0 14 11"><rect width="14" height="11" rx="1" fill="var(--orange)"/><path d="M0 1 L7 6 L14 1" fill="none" stroke="var(--black)" stroke-width="1.2"/></svg>hello@pdworks.net</div>
  </div>
  <nav class="foot-links">
    <a href="#">Home</a><a href="#">Our Work</a><a href="#">Capabilities</a><a href="#">About Us</a><a href="#">Blog</a>
  </nav>
  <p class="copyright">©Copyrights 2021 Penfield Draft Works &nbsp;| &nbsp; All Rights Reserved</p>
</footer>

</body>
</html>
```